Brochure 11 x 25.5 Trifold

Harbor Lane Associates, Inc. is a payroll, benefits, and HR administration company. We are in need of a brochure to showcase all of our services. Attached is a one-page information sheet that contains the information we want in the brochure as well as several images. The brochure is a 11 x 25.5 tri-fold (a sample is attached). Please use the colors in the attached logo and design to complement our website harborlanehq.com.
Target Market(s)
Company executives
Industry/Entity Type
Human Resource Management
Font styles to use
Other font styles liked:
- Avenir LT
Colors
Designer to choose colors to be used in the design.

```html
<!DOCTYPE html>
<html lang="en">
<head>
<meta charset="utf-8">
<title>Harbor Lane Associates – Trifold Outside</title>
<link href="https://fonts.googleapis.com/css2?family=Montserrat:wght@300;400;500;600;700&family=Nunito:wght@800;900&display=swap" rel="stylesheet">
<style>
  :root {
    --page: #d6d6d6;
    --paper: #f4f4f3;
    --navy: #1c3a5c;
    --navy-deep: #163552;
    --green: #8cac33;
    --green-dark: #7a9a2a;
    --text: #2a2a2a;
    --orange: #f3a62a;
    --red: #ea5b3a;
    --olive: #a9a437;
    --sky: #5fb7d8;
    --teal: #2a9bb0;
    --ink: #1d2e5c;
  }
  * { margin: 0; padding: 0; box-sizing: border-box; }
  html, body { width: 1108px; height: 1200px; overflow: hidden; background: var(--page); }
  body { position: relative; font-family: "Montserrat", Arial, sans-serif; color: var(--text); }

  .brochure {
    position: absolute; left: 34px; top: 376px;
    width: 1040px; height: 448px;
    background: var(--paper);
    overflow: hidden;
    box-shadow: 0 4px 14px rgba(0,0,0,.18);
  }
  .brochure__art { position: absolute; inset: 0; width: 1040px; height: 448px; }

  .tagline {
    position: absolute; left: 30px; top: 186px; width: 310px;
    font-family: "Nunito", Arial, sans-serif; font-weight: 900;
    font-size: 22px; line-height: 26px; color: var(--navy);
    text-align: center; letter-spacing: -0.2px;
  }
  .intro {
    position: absolute; left: 44px; top: 243px; width: 282px;
    font-size: 6.9px; line-height: 10.7px; color: var(--text);
  }

  .brand { position: absolute; left: 694px; top: 36px; }
  .brand__dot {
    position: absolute; left: 0; top: 6px; width: 46px; height: 46px;
    border-radius: 50%; background: var(--navy);
  }
  .brand__name {
    position: absolute; left: 58px; top: 8px; white-space: nowrap;
    font-weight: 300; font-size: 24px; line-height: 26px; color: var(--navy);
  }
  .brand__sub {
    position: absolute; left: 60px; top: 38px; white-space: nowrap;
    font-weight: 300; font-size: 14px; letter-spacing: 6px; color: var(--green);
  }

  .promise { position: absolute; left: 706px; top: 126px; }
  .promise__lead {
    font-weight: 600; font-size: 13px; line-height: 16px; color: var(--navy);
    letter-spacing: .3px;
  }
  .promise__focus {
    margin-top: 2px; font-weight: 700; font-size: 20.5px; line-height: 24px;
    color: var(--green); letter-spacing: .2px;
  }

  .web-bar {
    position: absolute; left: 737px; top: 425px; width: 246px; height: 23px;
    background: var(--navy-deep); border-top-left-radius: 8px; border-top-right-radius: 3px;
    color: #fff; font-size: 10px; letter-spacing: 2.6px; font-weight: 500;
    text-align: center; line-height: 24px;
  }

  .cycle-label { font-family: "Montserrat", Arial, sans-serif; font-size: 5.6px; fill: #222; }
  .cycle-title { font-family: "Montserrat", Arial, sans-serif; font-size: 5.6px; font-weight: 500; }
  .cycle-core { font-family: "Montserrat", Arial, sans-serif; font-size: 7.6px; font-weight: 500; fill: var(--navy); }
  .cycle-num { font-family: "Montserrat", Arial, sans-serif; font-size: 3.6px; font-weight: 600; }
</style>
</head>
<body>
<section class="brochure" aria-label="Trifold brochure, outside spread">
  <svg class="brochure__art" viewBox="0 0 1040 448" xmlns="http://www.w3.org/2000/svg">
    <defs>
      <linearGradient id="teamPhoto" x1="0" y1="0" x2="1" y2="1">
        <stop offset="0" stop-color="#b9c3cc"/>
        <stop offset=".45" stop-color="#6f95b6"/>
        <stop offset="1" stop-color="#1e5c8e"/>
      </linearGradient>
      <linearGradient id="meetingPhoto" x1="0" y1="0" x2="1" y2="1">
        <stop offset="0" stop-color="#4d5358"/>
        <stop offset=".5" stop-color="#2f3a44"/>
        <stop offset="1" stop-color="#9a8d7c"/>
      </linearGradient>
    </defs>

    <!-- left panel photo -->
    <path role="img" aria-label="Photo of a smiling businessman with colleagues at a laptop, blue tint"
          d="M0,0 H355 C322,10 300,40 286,80 C266,140 200,175 120,172 C60,170 20,150 0,125 Z"
          fill="url(#teamPhoto)"/>

    <!-- software on laptop and phone -->
    <g role="img" aria-label="HR software dashboard shown on a laptop and a phone">
      <rect x="74" y="307" width="214" height="132" rx="5" fill="#1f2227"/>
      <rect x="81" y="313" width="200" height="118" fill="#eef1f4"/>
      <rect x="81" y="313" width="32" height="118" fill="#e1e5ea"/>
      <rect x="74" y="434" width="214" height="6" fill="#34383e"/>
      <rect x="262" y="352" width="48" height="93" rx="5" fill="#1f2227"/>
      <rect x="266" y="360" width="40" height="77" fill="#e9edf1"/>
    </g>

    <!-- right panel green wave and photo -->
    <path d="M420,448 C470,390 520,340 573,323 C680,290 760,260 822,225 C860,200 880,150 910,115 C940,92 990,88 1040,88 V152 C990,160 930,200 862,258 C790,320 700,380 580,448 Z"
          fill="var(--green)"/>
    <path role="img" aria-label="Photo of a business meeting with an executive reviewing a report"
          d="M580,448 C700,380 790,320 862,258 C930,200 990,160 1040,152 V448 Z"
          fill="url(#meetingPhoto)"/>

    <!-- employee lifecycle diagram -->
    <g class="cycle">
      <g stroke-width="5" fill="none">
        <path d="M512,143 A38,38 0 0 1 544.9,162" stroke="var(--orange)"/>
        <path d="M544.9,162 A38,38 0 0 1 544.9,200" stroke="var(--olive)"/>
        <path d="M544.9,200 A38,38 0 0 1 512,219" stroke="var(--sky)"/>
        <path d="M512,219 A38,38 0 0 1 479.1,200" stroke="var(--teal)"/>
        <path d="M479.1,200 A38,38 0 0 1 479.1,162" stroke="var(--ink)"/>
        <path d="M479.1,162 A38,38 0 0 1 512,143" stroke="var(--red)"/>
      </g>
      <g stroke-width="1.6">
        <line x1="512" y1="143" x2="512" y2="124" stroke="var(--orange)"/>
        <line x1="544.9" y1="162" x2="560" y2="154" stroke="var(--olive)"/>
        <line x1="544.9" y1="200" x2="554" y2="207" stroke="var(--sky)"/>
        <line x1="512" y1="219" x2="511" y2="232" stroke="var(--teal)"/>
        <line x1="479.1" y1="200" x2="461" y2="208" stroke="var(--ink)"/>
        <line x1="479.1" y1="162" x2="461" y2="148" stroke="var(--red)"/>
      </g>

      <g fill="#fff" stroke-width="1.8">
        <circle cx="512" cy="110" r="13" stroke="var(--orange)"/>
        <circle cx="572" cy="149" r="13" stroke="var(--olive)"/>
        <circle cx="566" cy="213" r="13" stroke="var(--sky)"/>
        <circle cx="511" cy="246" r="13" stroke="var(--teal)"/>
        <circle cx="449" cy="214" r="13" stroke="var(--ink)"/>
        <circle cx="449" cy="141" r="13" stroke="var(--red)"/>
      </g>
      <!-- simple icons -->
      <g fill="var(--orange)"><circle cx="508" cy="106" r="2.4"/><circle cx="516" cy="106" r="2.4"/><path d="M503,116 a5,4 0 0 1 10,0 Z M511,116 a5,4 0 0 1 10,0 Z"/></g>
      <text x="572" y="153" text-anchor="middle" font-family="Montserrat, sans-serif" font-size="11" font-weight="700" fill="var(--olive)">$</text>
      <g fill="var(--sky)"><circle cx="566" cy="209" r="3"/><path d="M559,220 a7,5 0 0 1 14,0 Z"/></g>
      <g fill="var(--teal)"><circle cx="511" cy="242" r="3"/><path d="M504,253 a7,5 0 0 1 14,0 Z"/></g>
      <g fill="none" stroke="var(--ink)" stroke-width="1.4"><path d="M444,208 h10 v12 h-10 Z"/><path d="M446.5,214 l2,2 l3,-4"/></g>
      <g fill="var(--red)"><circle cx="445" cy="138" r="2.4"/><circle cx="453" cy="138" r="2.4"/><path d="M440,148 a5,4 0 0 1 10,0 Z M448,148 a5,4 0 0 1 10,0 Z"/></g>

      <g fill="#fff" stroke-width="1">
        <circle cx="512" cy="143" r="4.5" stroke="var(--orange)"/>
        <circle cx="544.9" cy="162" r="4.5" stroke="var(--olive)"/>
        <circle cx="544.9" cy="200" r="4.5" stroke="var(--sky)"/>
        <circle cx="512" cy="219" r="4.5" stroke="var(--teal)"/>
        <circle cx="479.1" cy="200" r="4.5" stroke="var(--ink)"/>
        <circle cx="479.1" cy="162" r="4.5" stroke="var(--red)"/>
      </g>
      <g class="cycle-num" text-anchor="middle">
        <text x="512" y="144.3" fill="var(--orange)">01</text>
        <text x="544.9" y="163.3" fill="var(--olive)">02</text>
        <text x="544.9" y="201.3" fill="var(--sky)">03</text>
        <text x="512" y="220.3" fill="var(--teal)">04</text>
        <text x="479.1" y="201.3" fill="var(--ink)">05</text>
        <text x="479.1" y="163.3" fill="var(--red)">06</text>
      </g>
      <text class="cycle-core" x="512" y="179" text-anchor="middle">EMPLOYEE</text>
      <text class="cycle-core" x="512" y="189" text-anchor="middle">LIFECYCLE</text>

      <g class="cycle-label" text-anchor="middle">
        <text x="512" y="58">Auto generate notice to</text>
        <text x="512" y="65.4">new-hire, standard and</text>
        <text x="512" y="72.8">customized forms and</text>
        <text x="512" y="80.2">acknowledgements</text>
        <text class="cycle-title" x="513" y="88" fill="var(--orange)">ONBOARDING</text>
      </g>
      <g class="cycle-label" text-anchor="end">
        <text class="cycle-title" x="423" y="129" fill="var(--red)">HIRING</text>
        <text x="423" y="136.4">Integrated</text>
        <text x="423" y="143.8">cloud-based ATS,</text>
        <text x="423" y="151.2">Auto post to job</text>
        <text x="423" y="158.6">boards, applicant</text>
        <text x="423" y="166">management &amp;</text>
        <text x="423" y="173.4">screening</text>
        <text class="cycle-title" x="423" y="197" fill="var(--ink)">SEPARATION</text>
        <text x="423" y="204.4">COBRA,</text>
        <text x="423" y="211.8">Retirement plan</text>
        <text x="423" y="219.2">assistance, DOL</text>
        <text x="423" y="226.6">Notices</text>
      </g>
      <g class="cycle-label">
        <text class="cycle-title" x="595" y="129" fill="var(--olive)">PAYROLL</text>
        <text x="595" y="136.4">HRIS, Direct deposits,</text>
        <text x="595" y="143.8">New Hire Reporting,</text>
        <text x="595" y="151.2">Employee Portal, Year</text>
        <text x="595" y="158.6">End Reporting</text>
        <text class="cycle-title" x="595" y="197" fill="var(--sky)">BENEFITS</text>
        <text x="595" y="204.4">Online enrollment,</text>
        <text x="595" y="211.8">application, benefit</text>
        <text x="595" y="219.2">reconciliations,</text>
        <text x="595" y="226.6">eligibility tracking</text>
        <text x="595" y="234">notifications,</text>
        <text x="595" y="241.4">retirement plan</text>
      </g>
      <g class="cycle-label" text-anchor="middle">
        <text class="cycle-title" x="511" y="274" fill="var(--teal)">EMPLOYEE MANAGEMENT</text>
        <text x="509" y="281.4">Culture development,</text>
        <text x="509" y="288.8">discipline, leave</text>
        <text x="509" y="296.2">management, Workers'</text>
        <text x="509" y="303.6">Compensation claims,</text>
        <text x="509" y="311">employee verifications,</text>
        <text x="509" y="318.4">handbook</text>
      </g>
    </g>
  </svg>

  <h1 class="tagline">FROM HIRE TO RETIRE,<br>WE’VE GOT YOU COVERED</h1>
  <p class="intro">Harbor Lane Associates has been delivering quality HR and Payroll services for over 25 years. Our dedicated team of professionals is focused on being the best service provider in the industry. Our goal is to relieve business executives of the challenges of managing a dynamic and growing workforce in today’s regulatory environment and give them the freedom to focus on what drives their business.</p>

  <div class="brand">
    <span class="brand__dot"></span>
    <span class="brand__name">HARBOR LANE</span>
    <span class="brand__sub">ASSOCIATES</span>
  </div>

  <div class="promise">
    <p class="promise__lead">YOUR SINGLE-SOURCE<br>SOLUTION FOR THE</p>
    <p class="promise__focus">ENTIRE<br>EMPLOYEE<br>LIFECYCLE</p>
  </div>

  <div class="web-bar">WWW.HARBORLANEHQ.COM</div>
</section>
</body>
</html>
```